Plakat-Design Workshop gegen Prüfungsangst
Zielgruppe
Prüfungsangst überwinden mittels Workshops: 'Selbsthypnose erlernen'
Zielgruppe Studenten
Schweißausbrüche, Blackout, und Resignation.
Viele kennen diese unangenehmen Momente, wenn eine Prüfung begonnen hat und die Aufgabenstellungen scheinbar unlösbar sind.
Dann ist Entspannung nahezu unmöglich. Das Stresshormon Cortisol wurde bereits ausgeschüttet. Es beeinträchtigt die Erinnerung an das Gelernte.
Die mentale Vorbereitung sollte schon viel eher ansetzen, wenn es noch nicht zu spät ist. Wenn der Körper noch nicht verkrampft ist.
Selbsthypnose vor Prüfungen ist hier eine tolle Möglichkeit.
Mit Hilfe einer geführten Selbsthypnoseanleitung ist es Dir möglich Dein Unterbewusstsein so zu programmieren, dass diese Übererregungszustände vor Prüfungssituationen deutlich reduziert werden.
Aufgabenstellung
DINA 4 Plakat, 'Prüfungsangst?' mit einem Freifeld, wo man Ort, Datum und Zeit der Veranstaltung 'Selbsthypnose erlernen'
(Selbstsicher in die Prüfung) eindrucken kann.
darunter:
Anmeldung: Tel: 01563 8074215
Dipl. Sportl. Henrik Wolde Mentaltraining
weitere Infos auch über Einzelsitzungen: www.wolde-trancepraxis.de

```html
<!DOCTYPE html>
<html lang="de">
<head>
<meta charset="utf-8">
<title>Prüfungsangst? – Selbsthypnose lernen</title>
<link rel="stylesheet" href="https://fonts.googleapis.com/css2?family=Montserrat:wght@400;500;600;700&display=swap">
<style>
  :root {
    --ink: #0a0a0a;
    --paper: #ffffff;
    --grey: #737373;
    --accent: #e2302b;
    --seal: #9ba2a8;
    --photo-warm: #b7763a;
    --photo-deep: #6e3f1c;
    --photo-cool: #8fa3bd;
  }
  * { margin: 0; padding: 0; box-sizing: border-box; }
  html, body { width: 848px; height: 1200px; overflow: hidden; background: var(--paper); }
  body { font-family: "Montserrat", sans-serif; color: var(--ink); }
  .poster { position: relative; width: 848px; height: 1200px; background: var(--paper); overflow: hidden; }

  .hero-photo {
    position: absolute; left: 0; top: 0; width: 848px; height: 525px;
    background:
      radial-gradient(ellipse at 70% 55%, var(--photo-cool) 0%, rgba(143,163,189,0) 45%),
      linear-gradient(120deg, var(--photo-warm) 0%, var(--photo-deep) 55%, var(--photo-warm) 100%);
  }

  .headline-band {
    position: absolute; left: 0; top: 468px; width: 609px; height: 103px;
    background: var(--ink);
  }
  .headline {
    position: absolute; left: 85px; top: 22px;
    color: var(--paper); font-weight: 500; font-size: 51px; letter-spacing: 3px; line-height: 1.1;
    white-space: nowrap;
  }

  .event-title { position: absolute; left: 77px; top: 640px; white-space: nowrap; }
  .event-title__main { font-weight: 700; font-size: 45px; line-height: 1.05; letter-spacing: 0.3px; }
  .event-title__sub { font-weight: 500; font-size: 37px; color: var(--grey); line-height: 1.25; }
  .bracket { position: absolute; width: 14px; height: 14px; border-color: var(--ink); border-style: solid; }
  .bracket--open { left: 67px; top: 636px; border-width: 1.5px 0 0 1.5px; }
  .bracket--close { left: 590px; top: 729px; border-width: 0 1.5px 1.5px 0; }

  .registration { position: absolute; left: 75px; top: 810px; white-space: nowrap; }
  .registration__label { font-weight: 700; font-size: 25px; margin-left: 2px; }
  .registration__phone { font-weight: 500; font-size: 27px; margin-top: 18px; letter-spacing: 0.5px; }
  .registration__line { font-weight: 500; font-size: 25px; line-height: 31px; margin-left: 2px; }
  .registration__line strong { font-weight: 700; }

  .fill-in { position: absolute; left: 513px; top: 791px; width: 275px; }
  .fill-in__row { display: flex; align-items: flex-end; font-size: 24px; font-weight: 500; height: 54px; }
  .fill-in__blank { flex: 1; border-bottom: 1.5px solid var(--ink); margin: 0 0 8px 18px; }
  .fill-in__blank--wide { margin-left: 30px; }

  .accent-rule { position: absolute; left: 0; top: 1002px; width: 743px; height: 9px; background: var(--accent); }

  .footer { position: absolute; left: 0; top: 1007px; width: 848px; height: 193px; background: var(--ink); }
  .certificate-seal {
    position: absolute; left: 77px; top: 1048px; width: 120px; height: 120px; border-radius: 50%;
    background: var(--seal);
  }
  .brand { position: absolute; left: 248px; top: 1116px; width: 255px; text-align: center; color: var(--paper); white-space: nowrap; }
  .brand__name { font-weight: 700; font-size: 19px; letter-spacing: 0.5px; line-height: 1.1; }
  .brand__tagline { font-weight: 500; font-size: 8.5px; letter-spacing: 1.2px; margin-top: 5px; text-transform: uppercase; }
  .more-info { position: absolute; left: 548px; top: 1086px; color: var(--paper); white-space: nowrap; }
  .more-info__label { font-weight: 400; font-size: 19px; }
  .more-info__url { font-weight: 700; font-size: 17px; margin-top: 8px; }
</style>
</head>
<body>
<main class="poster">
  <div class="hero-photo" role="img" aria-label="Foto: Studentin in einer Prüfungshalle stützt den Kopf in die Hände, im Hintergrund schreiben weitere Prüflinge"></div>

  <div class="headline-band">
    <h1 class="headline">Prüfungsangst?</h1>
  </div>

  <span class="bracket bracket--open"></span>
  <div class="event-title">
    <h2 class="event-title__main">SELBSTHYPNOSE LERNEN</h2>
    <p class="event-title__sub">Selbstsicher in die Prüfung</p>
  </div>
  <span class="bracket bracket--close"></span>

  <section class="registration">
    <p class="registration__label">Anmeldung:</p>
    <p class="registration__phone">01563 8074215</p>
    <p class="registration__line">Dipl. Sportl.</p>
    <p class="registration__line"><strong>Henrik Wolde</strong> Mentaltraining</p>
  </section>

  <section class="fill-in">
    <div class="fill-in__row"><span>Ort:</span><span class="fill-in__blank fill-in__blank--wide"></span></div>
    <div class="fill-in__row"><span>Datum:</span><span class="fill-in__blank"></span></div>
    <div class="fill-in__row"><span>Uhrzeit:</span><span class="fill-in__blank"></span></div>
  </section>

  <div class="footer"></div>
  <div class="accent-rule"></div>
  <div class="certificate-seal" role="img" aria-label="Platz für ein Zertifizierungssiegel"></div>
  <div class="brand">
    <p class="brand__name">WOLDE-TRANCEPRAXIS</p>
    <p class="brand__tagline">Ruhe finden – Stärke entdecken</p>
  </div>
  <div class="more-info">
    <p class="more-info__label">weitere Infos unter:</p>
    <p class="more-info__url">www.wolde-trancepraxis.de</p>
  </div>
</main>
</body>
</html>
```